Marlow Estate Fixers (Handyman / Home Improvement Company)

Looking for a double sided professional looking business card with Logo attached to be highlighted on one side and throwing in an image of a handyman as an option would be nice to see as well. We are a company focused on providing quality Handyman and Home improvement services in a timely manner that is done right the first time with integrity

Industry/Entity Type

Handyman / Home Improvement

Contact Information for Business Card

(LOGO, Name, Mobile and office phone numbers, email) on front side of card, (the words "The SOLUTION to all of your Handyman and Home Improvement needs" followed by "Family Owned and Operated" at the very bottom) on the back.

Colors
EB3D1F
EC4F4E
F09395
F8D3D4
FCEDEE

Requirements
Must have
• Red, Gray, Black Color scheme
Should not have
• No Yellow or Blue colors

```html
<!DOCTYPE html>
<html lang="en">
<head>
<meta charset="utf-8">
<title>Marlow Estate Fixers — Business Card</title>
<link rel="stylesheet" href="https://fonts.googleapis.com/css2?family=Montserrat:wght@400;600;700;800&display=swap">
<style>
  :root {
    --bg: #2b2b2b;
    --card: #1c1c1d;
    --card-back: #111112;
    --red: #e8312a;
    --white: #ffffff;
    --muted: #d9d9d9;
    --soft: #9a9a9a;
    --gloss-a: #1a1a1b;
    --gloss-b: #0b0b0c;
  }
  * { margin: 0; padding: 0; box-sizing: border-box; }
  html, body { width: 1200px; height: 875px; overflow: hidden; }
  body {
    background: var(--bg);
    font-family: "Montserrat", Arial, sans-serif;
    position: relative;
  }
  .card {
    position: absolute;
    width: 620px;
    height: 354px;
    border-radius: 22px;
    overflow: hidden;
    box-shadow: 0 18px 40px rgba(0,0,0,.45);
  }

  /* Back side */
  .card-back { left: 60px; top: 60px; background: var(--card-back); }
  .gloss-pattern {
    position: absolute; inset: 0;
    background: linear-gradient(135deg, var(--gloss-a) 0%, var(--gloss-b) 60%, var(--gloss-a) 100%);
  }
  .back-brand {
    position: absolute; right: 56px; top: 132px;
    display: flex; align-items: center; gap: 8px;
  }
  .back-brand .mark { width: 14px; height: 14px; border-radius: 50%; background: var(--red); flex: none; }
  .back-brand .name {
    color: var(--white); font-weight: 800; font-size: 15px;
    letter-spacing: .5px; text-transform: uppercase;
  }
  .back-tagline {
    position: absolute; left: 42px; top: 196px; width: 330px;
    color: var(--white); font-weight: 700; font-size: 17px; line-height: 1.35;
  }
  .back-tagline .accent { color: var(--red); }
  .back-family {
    position: absolute; left: 0; right: 0; bottom: 24px;
    text-align: center; color: var(--soft);
    font-weight: 600; font-size: 12px; letter-spacing: 3px; text-transform: uppercase;
  }

  /* Front side */
  .card-front { left: 520px; top: 460px; background: var(--card); }
  .person { position: absolute; left: 42px; top: 118px; }
  .person-name { font-size: 27px; font-weight: 800; color: var(--white); line-height: 1; }
  .person-name .surname { color: var(--red); }
  .person-role { font-size: 14px; color: var(--muted); margin-top: 6px; }
  .address {
    position: absolute; left: 42px; top: 206px;
    font-size: 14px; color: var(--muted); line-height: 1.35;
  }
  .contacts { position: absolute; left: 42px; top: 262px; list-style: none; }
  .contacts li {
    display: flex; align-items: center; gap: 10px;
    font-size: 14px; color: var(--white); line-height: 1.6;
  }
  .contacts svg { width: 13px; height: 13px; fill: var(--red); flex: none; }
  .front-brand {
    position: absolute; right: 40px; top: 70px; width: 250px;
    display: flex; align-items: center; gap: 12px;
  }
  .front-brand .mark { width: 34px; height: 34px; border-radius: 50%; background: var(--red); flex: none; }
  .front-brand .name {
    color: var(--white); font-weight: 800; font-size: 30px;
    line-height: 1.05; text-transform: uppercase;
  }
</style>
</head>
<body>
  <section class="card card-back">
    <div class="gloss-pattern" role="img" aria-label="Spot-gloss repeated brand pattern on black"></div>
    <div class="back-brand">
      <span class="mark"></span>
      <span class="name">Marlow Estate Fixers</span>
    </div>
    <p class="back-tagline">The <span class="accent">SOLUTION</span> to all of your Handyman and Home Improvement needs</p>
    <p class="back-family">Family Owned and Operated</p>
  </section>

  <section class="card card-front">
    <div class="person">
      <p class="person-name">Dale <span class="surname">Brenner</span></p>
      <p class="person-role">Managing Director</p>
    </div>
    <p class="address">48 Harlow Lane,<br>Brookfield, USA</p>
    <ul class="contacts">
      <li>
        <svg viewBox="0 0 24 24" aria-hidden="true"><path d="M6.6 10.8a15.1 15.1 0 0 0 6.6 6.6l2.2-2.2a1 1 0 0 1 1-.25 11.4 11.4 0 0 0 3.6.57 1 1 0 0 1 1 1V20a1 1 0 0 1-1 1A17 17 0 0 1 3 4a1 1 0 0 1 1-1h3.5a1 1 0 0 1 1 1c0 1.25.2 2.45.57 3.57a1 1 0 0 1-.25 1z"/></svg>
        (08) 5550 1824
      </li>
      <li>
        <svg viewBox="0 0 24 24" aria-hidden="true"><path d="M2 5h20v14H2zm2 2v.5l8 5 8-5V7l-8 5z"/></svg>
        hello@marlowfixers.com
      </li>
      <li>
        <svg viewBox="0 0 24 24" aria-hidden="true"><path d="M12 2a10 10 0 1 0 0 20 10 10 0 0 0 0-20zm0 2c.9 1.2 1.6 2.6 2 4h-4c.4-1.4 1.1-2.8 2-4zM4.3 14a8 8 0 0 1 0-4h3.3a17 17 0 0 0 0 4zm.9 2h2.9c.3 1.3.8 2.5 1.4 3.6A8 8 0 0 1 5.200 16zm2.9-8H5.2a8 8 0 0 1 4.3-3.6C8.9 5.5 8.4 6.7 8.1 8zM12 20c-.9-1.2-1.6-2.6-2-4h4c-.4 1.4-1.1 2.8-2 4zm2.3-6H9.7a15 15 0 0 1 0-4h4.6a15 15 0 0 1 0 4zm.2 5.6c.6-1.1 1.1-2.3 1.4-3.6h2.9a8 8 0 0 1-4.3 3.6zm1.9-5.6a17 17 0 0 0 0-4h3.3a8 8 0 0 1 0 4z"/></svg>
        www.marlowfixers.com
      </li>
    </ul>
    <div class="front-brand">
      <span class="mark"></span>
      <span class="name">Marlow Estate Fixers</span>
    </div>
  </section>
</body>
</html>
```